Oil Field Service company needs professional business cards

Looking to clean up our current company business cards and look a little more professional. Brenwick Casing Services is a US based company that services the oil field. We deal with engineers, managers and oil rigs....................................................................................................................................................................................................................................................................................................................................................................................................

Target Market(s)

Oil and Gas professionals

Industry/Entity Type

Oil And Gas

Contact Information for Business Card

See attached photo as example

Font styles to use
Sans Serif

Colors
ec1f27

Requirements
Must have
• Company Logo, Name, Title, Cell, Office, Fax, Email.
• See attached photo
Nice to have
• External CRT, Internal CRT, Casing Crews, Torque Turn, Laydown Machine
Should not have
• Do not introduce any new pictures and keep it professional looking

```html
<!DOCTYPE html>
<html lang="en">
<head>
<meta charset="utf-8">
<title>Brenwick Casing Services – Business Card</title>
<link href="https://fonts.googleapis.com/css2?family=Lato:wght@400;700;900&display=swap" rel="stylesheet">
<style>
  :root {
    --bg-top: #262626;
    --bg-bottom: #040404;
    --card-white: #ffffff;
    --slate: #45545f;
    --slate-text: #3b4a55;
    --brand-red: #ec1f27;
    --ink: #1f1f1f;
    --rule: #b9b9b9;
  }
  * { margin: 0; padding: 0; box-sizing: border-box; }
  html, body { width: 1200px; height: 900px; overflow: hidden; }
  body {
    background: linear-gradient(180deg, var(--bg-top) 0%, #141414 55%, var(--bg-bottom) 100%);
    font-family: "Lato", sans-serif;
    position: relative;
  }
  .card {
    position: absolute;
    top: 306px;
    width: 439px;
    height: 271px;
    border-radius: 12px;
  }
  .card-front { left: 149px; background: var(--card-white); }
  .card-back { left: 609px; background: var(--slate); }

  .wordmark {
    position: absolute;
    left: 28px;
    top: 40px;
    display: flex;
    align-items: center;
    gap: 10px;
    color: var(--slate-text);
    font-weight: 900;
    font-size: 22px;
    letter-spacing: 0.5px;
    text-transform: uppercase;
  }
  .wordmark-square {
    width: 14px; height: 14px;
    background: var(--brand-red);
  }

  .person {
    position: absolute;
    right: 20px;
    top: 103px;
    text-align: right;
  }
  .person-name { color: var(--brand-red); font-weight: 700; font-size: 15px; line-height: 18px; }
  .person-title { color: var(--ink); font-size: 12px; line-height: 15px; }

  .divider {
    position: absolute;
    left: 28px; right: 21px; top: 148px;
    border-top: 1.5px solid var(--rule);
  }

  .contact-list {
    position: absolute;
    left: 28px;
    top: 158px;
    list-style: none;
  }
  .contact-list li {
    display: flex;
    align-items: center;
    gap: 8px;
    height: 16px;
    font-size: 12.5px;
    color: var(--ink);
  }
  .contact-list svg { width: 9px; height: 9px; fill: var(--brand-red); flex: none; }

  .services {
    position: absolute;
    left: 0; right: 0; top: 233px;
    text-align: center;
    font-size: 12.5px;
    color: var(--slate-text);
  }

  .back-wordmark {
    position: absolute;
    left: 0; right: 0; top: 112px;
    text-align: center;
    color: var(--card-white);
    font-weight: 900;
    font-size: 30px;
    letter-spacing: 1px;
    text-transform: uppercase;
  }
</style>
</head>
<body>

  <section class="card card-front">
    <div class="wordmark"><span class="wordmark-square"></span>Brenwick Casing Services</div>

    <div class="person">
      <p class="person-name">Cody Marlowe</p>
      <p class="person-title">Area Manager</p>
    </div>

    <div class="divider"></div>

    <ul class="contact-list">
      <li>
        <svg viewBox="0 0 10 10" aria-hidden="true"><path d="M2 0.5 L3.6 2.6 L2.7 3.6 C3.3 5 5 6.7 6.4 7.3 L7.4 6.4 L9.5 8 L8.4 9.5 C4.5 9.2 0.8 5.5 0.5 1.6 Z"/></svg>
        (555) 214-6700
      </li>
      <li>
        <svg viewBox="0 0 10 10" aria-hidden="true"><path d="M2.8 0 H7.2 V10 H2.8 Z M3.6 1.2 V7.6 H6.4 V1.2 Z"/></svg>
        (555) 382-1946
      </li>
      <li>
        <svg viewBox="0 0 10 10" aria-hidden="true"><path d="M2.5 0 H7 V3 H9.5 V9.5 H0.5 V3 H2.5 Z M3.3 0.8 V3 H6.2 V0.8 Z M5 4.5 V6 H8.5 V4.5 Z"/></svg>
        (555) 214-6731
      </li>
      <li>
        <svg viewBox="0 0 10 10" aria-hidden="true"><path d="M0.5 2 H9.5 V8.5 H0.5 Z M1.2 2.6 L5 5.6 L8.8 2.6 Z" fill-rule="evenodd"/></svg>
        cmarlowe@brenwickcasing.com
      </li>
    </ul>

    <p class="services">Laydown Machine | Casing Crew | Mud Tool | Torque Turn</p>
  </section>

  <section class="card card-back">
    <div class="back-wordmark">Brenwick Casing Services</div>
  </section>

</body>
</html>
```